Business card for Luxury Portable Restroom Trailer company

We are a Luxury Portable Restroom Trailer Company Called FALCRIDGE HIRES. Based in Orange County California. We provide portable restroom trailers for events, such as, Weddings, Concerts, Charity events, Sporting events, Tournaments, Corporate events, ect. We rent and Sell the Luxury restrooms. Our colors are white, grey, and Orange. As you will see in the logo we uploaded.
There are 2 people in the company so the names and titles will change for the 3 people but card will remain the same. Here is the information for each Person: Dwight Penner CFO 555 318-0476
next Person: Leon Marchetti VP 555 318-0476
Next Person: Owen Marchetti CEO 555 318-0476
Information to include on the card: Luxury Restroom Trailers Rental and Sales. Weddings, Concerts, Charity, Sporting and Corp. Events.

```html
<!DOCTYPE html>
<html lang="en">
<head>
<meta charset="utf-8">
<title>Falcridge Hires – Business Card</title>
<link rel="stylesheet" href="https://fonts.googleapis.com/css2?family=Montserrat:wght@500;600;800;900&display=swap">
<style>
  :root {
    --orange: #f26d23;
    --white: #ffffff;
    --grey: #5a5a5a;
    --ink: #1c1c1c;
    --backdrop: #d9d9d9;
  }
  * { margin: 0; padding: 0; box-sizing: border-box; }
  html, body { width: 1200px; height: 856px; overflow: hidden; }
  body {
    background: var(--backdrop);
    font-family: "Montserrat", sans-serif;
    display: flex;
    flex-direction: column;
    align-items: center;
    justify-content: center;
    gap: 56px;
  }
  .card {
    width: 560px;
    height: 320px;
    position: relative;
    overflow: hidden;
    box-shadow: 0 10px 24px rgba(0,0,0,.25);
  }

  /* Front */
  .card-front { background: var(--white); }
  .emblem-panel {
    position: absolute;
    top: 0; right: 0;
    width: 210px; height: 100%;
    background: var(--orange);
  }
  .emblem {
    position: absolute;
    top: 50%; right: 105px;
    transform: translate(50%, -50%);
    width: 220px; height: 220px;
  }
  .contact-side {
    position: absolute;
    left: 34px; top: 30px;
  }
  .wordmark-small {
    font-weight: 800;
    font-size: 20px;
    letter-spacing: 1px;
    color: var(--grey);
    margin-bottom: 18px;
  }
  .person { margin-bottom: 12px; }
  .person-name {
    font-weight: 800;
    font-size: 17px;
    letter-spacing: .5px;
    color: var(--orange);
    text-transform: uppercase;
    line-height: 1.15;
  }
  .person-title {
    font-weight: 600;
    font-size: 13px;
    color: var(--ink);
    line-height: 1.3;
  }
  .person-phone {
    display: flex;
    align-items: center;
    gap: 6px;
    font-weight: 500;
    font-size: 13px;
    color: var(--ink);
  }
  .person-phone svg { width: 13px; height: 13px; }

  /* Back */
  .card-back {
    background: var(--orange);
    color: var(--white);
    display: flex;
    flex-direction: column;
    align-items: center;
    justify-content: center;
    gap: 34px;
  }
  .wordmark-large {
    font-weight: 900;
    font-size: 44px;
    letter-spacing: 2px;
    line-height: 1;
  }
  .services {
    list-style: none;
    text-align: center;
    font-weight: 500;
    font-size: 14px;
    line-height: 1.7;
  }
  .services li { display: inline; }
  .services li::before {
    content: "";
    display: inline-block;
    width: 7px; height: 7px;
    border-radius: 50%;
    background: var(--white);
    margin: 0 7px 2px 10px;
    vertical-align: middle;
  }
</style>
</head>
<body>

  <section class="card card-front">
    <div class="emblem-panel"></div>
    <svg class="emblem" viewBox="0 0 220 220" aria-hidden="true">
      <circle cx="110" cy="110" r="106" fill="var(--white)"/>
      <circle cx="110" cy="110" r="96" fill="none" stroke="var(--orange)" stroke-width="6"/>
      <circle cx="110" cy="110" r="84" fill="var(--orange)"/>
      <text x="110" y="117" text-anchor="middle" font-family="Montserrat, sans-serif" font-weight="800" font-size="20" fill="var(--white)">FALCRIDGE</text>
    </svg>

    <div class="contact-side">
      <div class="wordmark-small">FALCRIDGE HIRES</div>

      <div class="person">
        <div class="person-name">Dwight Penner</div>
        <div class="person-title">CFO</div>
        <div class="person-phone">
          <svg viewBox="0 0 24 24"><path fill="var(--orange)" d="M6.6 10.8a15.1 15.1 0 0 0 6.6 6.6l2.2-2.2c.3-.3.7-.4 1-.2 1.1.4 2.3.6 3.6.6.6 0 1 .4 1 1V20c0 .6-.4 1-1 1A17 17 0 0 1 3 4c0-.6.4-1 1-1h3.5c.6 0 1 .4 1 1 0 1.3.2 2.5.6 3.6.1.3 0 .7-.2 1z"/></svg>
          555 318-0476
        </div>
      </div>

      <div class="person">
        <div class="person-name">Leon Marchetti</div>
        <div class="person-title">VP</div>
        <div class="person-phone">
          <svg viewBox="0 0 24 24"><path fill="var(--orange)" d="M6.6 10.8a15.1 15.1 0 0 0 6.6 6.6l2.2-2.2c.3-.3.7-.4 1-.2 1.1.4 2.3.6 3.6.6.6 0 1 .4 1 1V20c0 .6-.4 1-1 1A17 17 0 0 1 3 4c0-.6.4-1 1-1h3.5c.6 0 1 .4 1 1 0 1.3.2 2.5.6 3.6.1.3 0 .7-.2 1z"/></svg>
          555 318-0476
        </div>
      </div>

      <div class="person">
        <div class="person-name">Owen Marchetti</div>
        <div class="person-title">CEO</div>
        <div class="person-phone">
          <svg viewBox="0 0 24 24"><path fill="var(--orange)" d="M6.6 10.8a15.1 15.1 0 0 0 6.6 6.6l2.2-2.2c.3-.3.7-.4 1-.2 1.1.4 2.3.6 3.6.6.6 0 1 .4 1 1V20c0 .6-.4 1-1 1A17 17 0 0 1 3 4c0-.6.4-1 1-1h3.5c.6 0 1 .4 1 1 0 1.3.2 2.5.6 3.6.1.3 0 .7-.2 1z"/></svg>
          555 318-0476
        </div>
      </div>
    </div>
  </section>

  <section class="card card-back">
    <div class="wordmark-large">FALCRIDGE HIRES</div>
    <ul class="services">
      <li>Luxury Restroom Trailers Rental and Sales</li><br>
      <li>Weddings</li><li>Concerts</li><li>Charity</li><li>Sporting and Corp</li><li>Events</li>
    </ul>
  </section>

</body>
</html>
```